Oil and Gas Exploration and Production company needs a business card design

We need a business card design using our logo and colors in the logo. We want a mainstream design.

```html
<!DOCTYPE html>
<html lang="en">
<head>
<meta charset="utf-8">
<title>Verada Oil &amp; Gas – Business Card</title>
<link href="https://fonts.googleapis.com/css2?family=Roboto:wght@400;700;900&display=swap" rel="stylesheet">
<style>
  :root {
    --gold: #c9a52c;
    --black: #111111;
    --white: #ffffff;
    --ink: #1a1a1a;
    --backdrop: #e9e6e0;
  }
  * { margin: 0; padding: 0; box-sizing: border-box; }
  html, body {
    width: 1200px; height: 780px; overflow: hidden;
    background: var(--backdrop);
    font-family: "Roboto", Arial, sans-serif;
  }
  .card {
    position: absolute; left: 100px; top: 105px;
    width: 1000px; height: 570px;
    background: var(--white);
    overflow: hidden;
    box-shadow: 0 10px 30px rgba(0,0,0,.18);
  }
  .card-bands { position: absolute; inset: 0; }
  .band-gold { fill: var(--gold); }
  .band-black { fill: var(--black); }

  .brand {
    position: absolute; left: 270px; top: 140px;
    display: flex; align-items: center; gap: 16px;
    white-space: nowrap;
  }
  .brand-dot {
    width: 40px; height: 40px; border-radius: 50%;
    background: var(--ink); flex: none;
  }
  .brand-name {
    font-weight: 900; font-size: 46px; color: var(--ink);
    letter-spacing: -0.5px; line-height: 1;
  }

  .person { position: absolute; left: 140px; top: 330px; }
  .person-name { font-weight: 900; font-size: 34px; color: var(--ink); line-height: 1.1; }
  .person-title { font-weight: 400; font-size: 24px; color: var(--gold); }

  .contact {
    position: absolute; left: 140px; top: 420px;
    font-size: 21px; color: var(--ink); line-height: 1.35; list-style: none;
  }
  .contact li { display: flex; align-items: center; gap: 10px; }
  .contact .icon { width: 20px; height: 20px; flex: none; }
  .icon-phone { fill: var(--gold); }
  .icon-mail rect { fill: var(--gold); }
  .icon-mail path { fill: none; stroke: var(--white); stroke-width: 1.6; }

  .website {
    position: absolute; right: 40px; bottom: 34px;
    font-size: 22px; color: var(--white); letter-spacing: .5px;
  }
</style>
</head>
<body>
  <section class="card" aria-label="Business card front">
    <svg class="card-bands" viewBox="0 0 1000 570" aria-hidden="true">
      <path class="band-gold" d="M0,0 L300,0 Q60,230 40,570 L0,570 Z"/>
      <path class="band-black" d="M760,0 Q1010,280 560,570 L1000,570 L1000,0 Z"/>
    </svg>

    <div class="brand">
      <span class="brand-dot"></span>
      <span class="brand-name">Verada Oil &amp; Gas</span>
    </div>

    <div class="person">
      <p class="person-name">Daniel Rhodes</p>
      <p class="person-title">President &amp; CEO</p>
    </div>

    <ul class="contact">
      <li>PO BOX 480, Harbour Road</li>
      <li>3rd Lane, Leeds</li>
      <li>
        <svg class="icon icon-phone" viewBox="0 0 24 24" aria-hidden="true"><path d="M6.6 10.8a15.1 15.1 0 0 0 6.6 6.6l2.2-2.2a1 1 0 0 1 1-.25 11.4 11.4 0 0 0 3.6.6 1 1 0 0 1 1 1V20a1 1 0 0 1-1 1A17 17 0 0 1 3 4a1 1 0 0 1 1-1h3.5a1 1 0 0 1 1 1 11.4 11.4 0 0 0 .6 3.6 1 1 0 0 1-.25 1z"/></svg>
        (123) 555 0188
      </li>
      <li>
        <svg class="icon icon-mail" viewBox="0 0 24 24" aria-hidden="true"><rect x="2" y="5" width="20" height="14"/><path d="M2 5l10 8 10-8"/></svg>
        hello@veradapetro.com
      </li>
    </ul>

    <p class="website">www.veradapetro.com</p>
  </section>
</body>
</html>
```